Realty Group Needs Classy, Contemporary Letterhead Design

We need a letterhead design for a new realty company located in NY, USA. We buy investment properties to rehabilitate and or keep in our rental portfolio.

```html
<!DOCTYPE html>
<html lang="en">
<head>
<meta charset="utf-8">
<title>Meridian Realty Group Letterhead</title>
<link rel="stylesheet" href="https://fonts.googleapis.com/css2?family=Open+Sans:wght@400;600;700&family=Lato:wght@400&display=swap">
<style>
  :root {
    --brand-purple: #4b2a8a;
    --band-gray: #7b7b7b;
    --ink: #3a3a3a;
    --ink-soft: #555555;
    --paper: #ffffff;
  }
  * { box-sizing: border-box; margin: 0; padding: 0; }
  html, body { width: 1040px; height: 1200px; overflow: hidden; background: var(--paper); }
  .letterhead {
    position: relative;
    width: 1040px;
    height: 1200px;
    background: var(--paper);
    font-family: "Open Sans", Arial, sans-serif;
    color: var(--ink);
  }
  .side-rule {
    position: absolute; left: 0; top: 0;
    width: 17px; height: 1200px;
    background: var(--brand-purple);
  }
  .brand {
    position: absolute; right: 106px; top: 60px;
    display: flex; align-items: center; gap: 10px;
    font-weight: 700; font-size: 26px;
    color: var(--brand-purple);
  }
  .brand-dot {
    width: 14px; height: 14px; border-radius: 50%;
    background: var(--brand-purple);
  }
  .letter-body {
    position: absolute; left: 99px; top: 0; width: 841px; height: 1000px;
    font-size: 16px; line-height: 20px; color: var(--ink-soft);
  }
  .letter-body > * { position: absolute; left: 0; width: 100%; }
  .issue-date { top: 216px; }
  .recipient { top: 252px; line-height: 19px; }
  .salutation { top: 357px; }
  .paragraph { text-align: justify; line-height: 27px; }
  .paragraph-one { top: 404px; }
  .paragraph-two { top: 566px; }
  .paragraph-three { top: 673px; }
  .closing { top: 815px; }
  .signature-mark {
    top: 854px; width: 240px; height: 24px;
    background: linear-gradient(90deg, #ececec, #dcdcdc);
    border-radius: 3px;
  }
  .signer-name { top: 893px; font-size: 20px; font-weight: 600; color: var(--ink); line-height: 26px; }
  .signer-role { top: 924px; }
  .footer-tabs { position: absolute; left: 0; top: 1010px; }
  .contact-list {
    position: absolute; left: 56px; top: 1050px;
    list-style: none;
    font-family: "Lato", Arial, sans-serif;
    font-size: 18px; color: #222222;
  }
  .contact-list li { height: 39.5px; line-height: 26px; }
  .address-band {
    position: absolute; left: 478px; top: 1113px;
    width: 562px; height: 40px;
    background: var(--band-gray);
    color: #ffffff;
    font-family: "Lato", Arial, sans-serif;
    font-size: 18px; line-height: 40px;
    padding-left: 42px;
  }
</style>
</head>
<body>
<main class="letterhead">
  <div class="side-rule"></div>

  <header class="brand">
    <span class="brand-dot"></span>
    <span class="brand-name">Meridian Realty Group, LLC</span>
  </header>

  <section class="letter-body">
    <p class="issue-date">Issuing Date: May 5, 2018</p>
    <p class="recipient">Name Of Employee Mr. XYZABC<br>Address of Employee<br>Address Line 2 etc..</p>
    <p class="salutation">Dear Mr.XYZABC</p>
    <p class="paragraph paragraph-one">Lorem Ipsum has been the industry's standard dummy text ever since the 1500s, when an unknown printer took a galley of type and scrambled it to make a type specimen book. It has survived not only five centuries, but also the leap into electronic typesetting, remaining essentially unchanged. It was popularised in the 1960s with the release of Lettrix sheets containing Lorem Ipsum passages, and more recently with desktop publishing software like Folio PageCraft including versions of Lorem Ipsum.</p>
    <p class="paragraph paragraph-two">Lorem Ipsum is simply dummy text of the printing and typesetting industry. Lorem Ipsum has been the industry's standard dummy text ever since the 1500s, when an unknown printer took a galley of type and scrambled it to make a type specimen book.</p>
    <p class="paragraph paragraph-three">It has survived not only five centuries, but also the leap into electronic typesetting, remaining essentially unchanged. It was popularised in the 1960s with the release of Lettrix sheets containing Lorem IpsumIpsum passages.</p>
    <p class="closing">Yours Sincerely</p>
    <span class="signature-mark" role="img" aria-label="Handwritten signature of Daniel Brooks"></span>
    <p class="signer-name">Daniel Brooks</p>
    <p class="signer-role">Managing Director</p>
  </section>

  <svg class="footer-tabs" width="60" height="190" viewBox="0 0 60 190" aria-hidden="true">
    <polygon points="0,0 17,0 17,3 47,22 47,190 0,190" fill="var(--brand-purple)"/>
    <polygon points="0,44 47,22 47,56 0,78" fill="var(--band-gray)"/>
    <polygon points="0,84 47,62 47,96 0,118" fill="var(--band-gray)"/>
    <polygon points="0,124 47,102 47,136 0,158" fill="var(--band-gray)"/>
    <path d="M19 42 q-2 8 6 14 l3 -3 -3 -3 -2 1 q-3 -3 -3 -6 l2 -1 -1 -4z" fill="#fff"/>
    <rect x="17" y="82" width="14" height="10" fill="none" stroke="#fff" stroke-width="1.5"/>
    <path d="M17 82 l7 6 7 -6" fill="none" stroke="#fff" stroke-width="1.5"/>
    <circle cx="24" cy="128" r="6" fill="#fff"/>
  </svg>

  <ul class="contact-list">
    <li>044-555 010 220</li>
    <li>hello@meridianrealty.com</li>
    <li>www.meridianrealty.com</li>
  </ul>

  <div class="address-band">87 Harbor Lane, New York, NY 10012</div>
</main>
</body>
</html>
```